Single Splash Web Page as Long Term Placeholder

I registered the url TideAndTaffy.com. This is the name of a business I will be starting several years down the road. It will be a coffee (drips) and ice cream (dips) store located in a beach town somewhere on the east coast of the US, probably in the Outer Banks of NC. I need a single page that will have the name of the business and the text:

Coming eventually to a beach near you!

The page should somehow reflect the beach environment.

```html
<!DOCTYPE html>
<html lang="en">
<head>
<meta charset="utf-8">
<title>Tide &amp; Taffy</title>
<link rel="stylesheet" href="https://fonts.googleapis.com/css2?family=Bitter:wght@700&display=swap">
<style>
  :root {
    --brand-green: #128a47;
    --ink: #141414;
    --band-white: #ffffff;
    --rule-white: rgba(255, 255, 255, 0.9);
    --sky-pale: #f3ecd2;
    --sky-gold: #f4d56e;
    --sun-core: #fff1b0;
    --horizon: #e9b94a;
    --sea: #d9c79a;
    --headland: #3a2f33;
    --sand-light: #d8b88e;
    --sand-mid: #b48a62;
    --sand-dark: #7a5a40;
  }
  * { margin: 0; padding: 0; box-sizing: border-box; }
  html, body {
    width: 1200px;
    height: 577px;
    overflow: hidden;
    background: var(--band-white);
    font-family: "Bitter", Georgia, serif;
  }
  .page {
    position: relative;
    width: 1200px;
    height: 577px;
  }
  .hero {
    position: absolute;
    left: 0; top: 0;
    width: 1200px;
    height: 358px;
  }
  .hero-photo {
    position: absolute;
    inset: 0;
    background:
      radial-gradient(ellipse 260px 90px at 260px 320px, var(--sun-core) 0%, rgba(255, 225, 120, 0.75) 40%, rgba(255, 215, 100, 0) 100%),
      radial-gradient(ellipse 420px 260px at 1080px 300px, rgba(40, 32, 36, 0.95) 0%, rgba(58, 47, 51, 0.75) 45%, rgba(58, 47, 51, 0) 100%),
      linear-gradient(90deg, rgba(0, 0, 0, 0) 55%, rgba(70, 55, 60, 0.35) 80%, rgba(40, 32, 36, 0.55) 100%),
      linear-gradient(180deg, var(--sky-pale) 0%, #f1e3b0 35%, var(--sky-gold) 68%, var(--horizon) 82%, var(--sea) 90%, #c9b489 100%);
  }
  .masthead {
    position: absolute;
    left: 0; top: 104px;
    width: 1200px;
    text-align: center;
  }
  .brand-name {
    color: var(--brand-green);
    font-size: 76px;
    font-weight: 700;
    line-height: 1;
  }
  .tagline {
    display: flex;
    align-items: center;
    justify-content: center;
    gap: 20px;
    margin-top: 16px;
  }
  .tagline-rule {
    width: 52px;
    height: 1px;
    background: var(--rule-white);
  }
  .tagline-text {
    color: var(--ink);
    font-size: 19px;
    font-weight: 700;
    letter-spacing: 4px;
  }
  .announcement {
    position: absolute;
    left: 0; top: 358px;
    width: 1200px;
    height: 49px;
    background: var(--band-white);
    display: flex;
    align-items: center;
    justify-content: center;
    color: var(--ink);
    font-size: 19px;
    font-weight: 700;
    white-space: pre;
  }
  .announcement .highlight { color: var(--brand-green); }
  .sand-strip {
    position: absolute;
    left: 0; top: 407px;
    width: 1200px;
    height: 21px;
    background:
      linear-gradient(180deg, rgba(255, 240, 210, 0.35), rgba(0, 0, 0, 0.1)),
      linear-gradient(90deg, var(--sand-light) 0%, var(--sand-mid) 55%, var(--sand-dark) 100%);
  }
  .menu-gallery {
    position: absolute;
    left: 0; top: 428px;
    width: 1200px;
    height: 149px;
    display: flex;
  }
  .menu-tile { flex: 1 1 150px; height: 100%; }
  .tile-cold-brew { background: linear-gradient(180deg, #ecebe8 0%, #8a6a58 60%, #4a3a30 100%); }
  .tile-choc-cone { background: linear-gradient(180deg, #3a3230 0%, #5e4330 55%, #8e6a48 100%); }
  .tile-coffee-splash { background: linear-gradient(180deg, #f6f8fb 0%, #c4d7e6 60%, #7f98ad 100%); }
  .tile-paper-cone { background: linear-gradient(180deg, #6f8a72 0%, #c9b796 55%, #8a7458 100%); }
  .tile-latte { background: linear-gradient(180deg, #5a3a26 0%, #b79a84 55%, #6a4a34 100%); }
  .tile-twin-cones { background: linear-gradient(180deg, #f5f0f1 0%, #a58a70 45%, #ecd99e 100%); }
  .tile-black-coffee { background: linear-gradient(180deg, #fbfaf7 0%, #bfa88e 55%, #f3efe8 100%); }
  .tile-scoop-plate { background: linear-gradient(180deg, #3e5a4c 0%, #d9e1dc 50%, #7a5a44 100%); }
</style>
</head>
<body>
<main class="page">
  <header class="hero">
    <div class="hero-photo" role="img" aria-label="Beach at sunset: golden sky and sun over the sea horizon, a dark wooded headland with leaning palm trees on the right"></div>
    <div class="masthead">
      <h1 class="brand-name">Tide &amp; Taffy</h1>
      <div class="tagline">
        <span class="tagline-rule"></span>
        <span class="tagline-text">COFFEE . ICE CREAMS . MORE</span>
        <span class="tagline-rule"></span>
      </div>
    </div>
  </header>

  <p class="announcement">Eventually coming to a beach near <span class="highlight">You!</span></p>

  <div class="sand-strip" role="img" aria-label="Strip of sandy beach"></div>

  <section class="menu-gallery">
    <div class="menu-tile tile-cold-brew" role="img" aria-label="Iced coffee with a carafe and jar of cream"></div>
    <div class="menu-tile tile-choc-cone" role="img" aria-label="Chocolate ice cream in a waffle cone"></div>
    <div class="menu-tile tile-coffee-splash" role="img" aria-label="Coffee splashing from a blue cup with beans"></div>
    <div class="menu-tile tile-paper-cone" role="img" aria-label="Ice cream cone on parchment paper with a scoop"></div>
    <div class="menu-tile tile-latte" role="img" aria-label="Latte with foam art in a white cup"></div>
    <div class="menu-tile tile-twin-cones" role="img" aria-label="Two chocolate dipped ice cream cones"></div>
    <div class="menu-tile tile-black-coffee" role="img" aria-label="Black coffee splashing in a white cup"></div>
    <div class="menu-tile tile-scoop-plate" role="img" aria-label="Ice cream scoops with sprinkles and a cone"></div>
  </section>
</main>
</body>
</html>
```